Stonebridge Building and Projects business cards

A business card with watermark background (construction work)

Company logo attached

Home improvement projects
House renovations
Bathroom and kitchen renovations
House extensions
New builds and granny flats

Director Omar Haddani
(Phone number)
omar@sbpbuilding.com.au
(Instagram logo) sbp_building

```html
<!DOCTYPE html>
<html lang="en">
<head>
<meta charset="utf-8">
<title>Stonebridge Building and Projects – Business Cards</title>
<link rel="stylesheet" href="https://fonts.googleapis.com/css2?family=Bebas+Neue&family=Nunito:wght@400;600&display=swap">
<style>
  :root {
    --backdrop: #3a3a3c;
    --card-white: #ffffff;
    --brand-blue: #3677b6;
    --ink-blue: #2e74b9;
    --ink-grey: #4a4a4a;
    --rule-grey: #d6d6d6;
    --band-text: #ffffff;
    --back-mark: #c4ecff;
  }
  * { margin: 0; padding: 0; box-sizing: border-box; }
  html, body { width: 1200px; height: 1200px; overflow: hidden; }
  body {
    background: var(--backdrop);
    font-family: "Nunito", sans-serif;
    position: relative;
  }
  .card {
    position: absolute;
    left: 262px;
    width: 686px;
    height: 392px;
    box-shadow: 0 18px 30px rgba(0,0,0,0.45);
    overflow: hidden;
  }
  .card--front { top: 165px; background: var(--card-white); }
  .card--back { top: 653px; background: var(--brand-blue); }

  .brand {
    position: absolute;
    display: flex;
    flex-direction: column;
    align-items: center;
    text-align: center;
  }
  .brand__square { background: currentColor; }
  .brand__name { font-weight: 600; line-height: 1.15; }

  .card--front .brand {
    left: 60px; top: 118px; width: 260px;
    color: var(--ink-blue);
  }
  .card--front .brand__square { width: 22px; height: 22px; margin-bottom: 12px; }
  .card--front .brand__name { font-size: 21px; }

  .divider {
    position: absolute;
    left: 303px; top: 96px;
    width: 1px; height: 163px;
    background: var(--rule-grey);
  }

  .person { position: absolute; left: 333px; top: 96px; }
  .person__name {
    font-family: "Bebas Neue", sans-serif;
    font-size: 33px;
    letter-spacing: 0.5px;
    color: var(--ink-blue);
    line-height: 1;
  }
  .person__role {
    font-size: 15px;
    color: var(--ink-grey);
    margin-top: 5px;
  }

  .contacts {
    position: absolute; left: 333px; top: 167px;
    list-style: none;
  }
  .contacts__item {
    display: flex; align-items: center;
    height: 20px;
    font-size: 15px;
    color: var(--ink-grey);
    letter-spacing: 0.3px;
  }
  .contacts__icon { width: 12px; height: 12px; margin-right: 9px; fill: var(--ink-blue); }

  .services {
    position: absolute;
    left: 0; top: 308px;
    width: 100%; height: 53px;
    background: var(--brand-blue);
    color: var(--band-text);
    font-size: 15px;
    text-align: center;
    padding-top: 6px;
    line-height: 19px;
  }
  .services__sep {
    display: inline-block;
    width: 6px; height: 6px;
    margin: 0 8px 2px;
    background:
      radial-gradient(circle, var(--band-text) 1.2px, transparent 1.4px) 0 0 / 3px 3px;
  }

  .card--back .brand {
    left: 0; top: 130px; width: 100%;
    color: var(--back-mark);
  }
  .card--back .brand__square { width: 36px; height: 36px; margin-bottom: 18px; }
  .card--back .brand__name { font-size: 30px; }
</style>
</head>
<body>
  <section class="card card--front">
    <div class="brand">
      <span class="brand__square"></span>
      <span class="brand__name">Stonebridge Building<br>and Projects</span>
    </div>

    <div class="divider"></div>

    <div class="person">
      <h1 class="person__name">Omar Haddani</h1>
      <p class="person__role">Director</p>
    </div>

    <ul class="contacts">
      <li class="contacts__item">
        <svg class="contacts__icon" viewBox="0 0 24 24"><path d="M6.6 10.8a15.1 15.1 0 0 0 6.6 6.6l2.2-2.2a1 1 0 0 1 1-.25 11.4 11.4 0 0 0 3.6.57 1 1 0 0 1 1 1V20a1 1 0 0 1-1 1A17 17 0 0 1 3 4a1 1 0 0 1 1-1h3.5a1 1 0 0 1 1 1c0 1.25.2 2.45.57 3.57a1 1 0 0 1-.25 1z"/></svg>
        369-555-0142
      </li>
      <li class="contacts__item">
        <svg class="contacts__icon" viewBox="0 0 24 24"><path d="M2 5h20v14H2zm2 2v.4l8 5 8-5V7zm0 2.8V17h16V9.8l-8 5z"/></svg>
        omar@sbpbuilding.com.au
      </li>
      <li class="contacts__item">
        <svg class="contacts__icon" viewBox="0 0 24 24"><path d="M12 2a10 10 0 1 0 0 20 10 10 0 0 0 0-20zm-1 17.9A8 8 0 0 1 4.1 10L9 15v1a2 2 0 0 0 2 2zm6.9-2.5A2 2 0 0 0 16 16h-1v-3a1 1 0 0 0-1-1H8v-2h2a1 1 0 0 0 1-1V7h2a2 2 0 0 0 2-2v-.4a8 8 0 0 1 2.9 12.8z"/></svg>
        www.sbpbuilding.com.au
      </li>
      <li class="contacts__item">
        <svg class="contacts__icon" viewBox="0 0 24 24"><circle cx="12" cy="12" r="10"/></svg>
        sbp_building
      </li>
    </ul>

    <div class="services">
      <p>Home improvement projects<span class="services__sep"></span>House renovations<span class="services__sep"></span>House extensions</p>
      <p>Bathroom &amp; kitchen renovations<span class="services__sep"></span>New builds &amp; granny flats</p>
    </div>
  </section>

  <section class="card card--back">
    <div class="brand">
      <span class="brand__square"></span>
      <span class="brand__name">Stonebridge Building<br>and Projects</span>
    </div>
  </section>
</body>
</html>
```